Bramblewood Card Company Business Cards

We are a trading card store with Glimmorax, sports and other TCG cards, we need a business card design that encompasses a clean cut, modern style with a retro flare. website is bramblewoodcardco.com for reference. Can utilize a comic book era feel or a more modern outdoor feel to utilize the "Pacific Northwest" elements of tress, mountains, etc.

Industry/Entity Type

Trading cards and collectibles

Contact Information for Business Card

business name, email address, phone number, name, owner job title

Font styles to use
Sans Serif

```html
<!DOCTYPE html>
<html lang="en">
<head>
<meta charset="utf-8">
<title>Bramblewood Card Company – Business Card</title>
<link rel="stylesheet" href="https://fonts.googleapis.com/css2?family=Montserrat:wght@400;500;700&display=swap">
<style>
  :root {
    --backdrop: #9c9c9c;
    --card: #ffffff;
    --cyan: #0fbfdf;
    --slate: #737373;
    --ink: #1b1b1b;
  }
  html, body {
    margin: 0;
    padding: 0;
    width: 1093px;
    height: 1200px;
    overflow: hidden;
    background: var(--backdrop);
    font-family: "Montserrat", sans-serif;
  }
  .stage { position: relative; width: 1093px; height: 1200px; }

  .card {
    position: absolute;
    left: 265px;
    width: 596px;
    height: 363px;
    background: var(--card);
    border-radius: 18px;
    overflow: hidden;
  }
  .card--front { top: 225px; }
  .card--back { top: 616px; height: 366px; }
  .card__band {
    position: absolute;
    left: 0; right: 0; bottom: 0;
    height: 18px;
    background: var(--cyan);
  }

  .brand {
    position: absolute;
    display: flex;
    flex-direction: column;
    align-items: center;
    justify-content: center;
    text-align: center;
    color: var(--slate);
    font-weight: 700;
    text-transform: uppercase;
  }
  .brand__dot {
    width: 14px; height: 14px;
    border-radius: 50%;
    background: var(--cyan);
    margin-bottom: 10px;
  }
  .brand--small { left: 80px; top: 127px; width: 180px; height: 152px; font-size: 17px; line-height: 1.25; letter-spacing: 1px; }
  .brand--large { left: 148px; top: 61px; width: 300px; height: 242px; font-size: 29px; line-height: 1.25; letter-spacing: 2px; }
  .brand--large .brand__dot { width: 22px; height: 22px; margin-bottom: 16px; }

  .divider {
    position: absolute;
    left: 269px; top: 125px;
    width: 2px; height: 150px;
    background: var(--cyan);
  }
  .contact { position: absolute; left: 282px; top: 118px; color: var(--ink); }
  .contact__name { margin: 0; font-size: 24px; font-weight: 700; color: var(--cyan); line-height: 1.2; }
  .contact__role { margin: 0 0 10px 1px; font-size: 13.5px; font-weight: 500; line-height: 1.2; }
  .contact__address { margin: 0 0 8px; font-size: 13.5px; font-weight: 500; line-height: 1.2; }
  .contact__list { list-style: none; margin: 0; padding: 0; font-size: 13.5px; font-weight: 500; }
  .contact__item { display: flex; align-items: center; height: 22px; }
  .contact__item svg { width: 13px; height: 13px; margin-right: 9px; flex: none; }
  .contact__item--phone svg { margin-right: 7px; }
</style>
</head>
<body>
<main class="stage">
  <section class="card card--front">
    <div class="brand brand--small">
      <span class="brand__dot"></span>
      Bramblewood<br>Card Company
    </div>
    <div class="divider"></div>
    <div class="contact">
      <h1 class="contact__name">Dorian Hale</h1>
      <p class="contact__role">Owner</p>
      <p class="contact__address">2480 Cedar Ridge Rd Suite<br>210 Tacoma, Ohio 44102</p>
      <ul class="contact__list">
        <li class="contact__item contact__item--phone">
          <svg viewBox="0 0 16 16" aria-hidden="true"><path fill="var(--cyan)" d="M3.6 1.2l2.3 2.6-1.3 1.6c.9 2 2.4 3.5 4.3 4.4l1.5-1.3 2.6 2.3-1.4 2.2C6.4 12.7 3.3 9.6 1.4 4.4z"/><path fill="none" stroke="var(--cyan)" stroke-width="1.2" d="M9.5 2.5a4 4 0 0 1 4 4M9.5 4.8a1.8 1.8 0 0 1 1.8 1.8"/></svg>
          06-48213957
        </li>
        <li class="contact__item">
          <svg viewBox="0 0 16 12" aria-hidden="true"><rect x="0" y="0" width="16" height="12" fill="var(--cyan)"/><path d="M0 0l8 6.5L16 0" fill="none" stroke="#fff" stroke-width="1.3"/></svg>
          info@bramblewoodcardcompany.com
        </li>
        <li class="contact__item">
          <svg viewBox="0 0 16 16" aria-hidden="true"><circle cx="8" cy="8" r="7.5" fill="var(--cyan)"/><path d="M4 4.5c1.5-.5 2.5.5 2 2s1.5 1 1.5 2.5-1 2-.5 3.5M10 3c.5 1.5 2 1.5 3 2.5" fill="none" stroke="#fff" stroke-width="1.3"/></svg>
          www.bramblewoodcardcompany.com
        </li>
      </ul>
    </div>
    <div class="card__band"></div>
  </section>

  <section class="card card--back">
    <div class="brand brand--large">
      <span class="brand__dot"></span>
      Bramblewood<br>Card Company
    </div>
    <div class="card__band"></div>
  </section>
</main>
</body>
</html>
```